Dental Practice Website design

Design a new website for Brambleford Dental Practice.
Design should be warm, neutral in colour, with some small amount of bright colour if needed but kept to a minimum. Website should look professional, high end. Home page should be easy to navigate and simple for patients to be able to book online.
Logo in files along with some examples of websites that we like. Please ask if any further info needed.
Menu should have:
About
New Patients
Treatments
Fees
Contact Us

Industry/Entity Type

Dentistry

Number of Pages Required

4 page

Font styles to use
Sans Serif

Colors

Designer to choose colors to be used in the design.

Requirements
Must have
• Ravelle ratings badge, book online button,
Nice to have
• neutral, relaxing colours
Should not have
• harsh, bright colours!

```html
<!DOCTYPE html>
<html lang="en">
<head>
<meta charset="utf-8">
<title>Brambleford Dental Practice</title>
<link href="https://fonts.googleapis.com/css2?family=Open+Sans:wght@400;600;700&display=swap" rel="stylesheet">
<style>
:root{
  --ink:#1d2b2e;
  --text:#4a4f52;
  --muted:#6b6f72;
  --line:#1d2b2e;
  --hero-bg:#e9e8e6;
  --panel:#e3e4e6;
  --photo-warm:#d9cfc4;
  --photo-cool:#cfdde6;
  --photo-grey:#e7e6e3;
  --star:#f2b13a;
  --white:#ffffff;
}
*{box-sizing:border-box;margin:0;padding:0}
html,body{width:1200px;height:3170px;overflow:hidden}
body{position:relative;font-family:"Open Sans",Arial,sans-serif;color:var(--text);background:var(--white)}
.abs{position:absolute}
.brand-name{font-family:"Open Sans",Arial,sans-serif;font-weight:400;color:var(--ink);text-align:center;line-height:1.1}
.btn{position:absolute;display:flex;align-items:center;justify-content:center;border-radius:18px;font-size:16px;height:34px}
.btn-dark{background:var(--ink);color:var(--white)}
.btn-outline{border:1.5px solid var(--ink);color:var(--ink);background:var(--white)}
h1,h2,h3{font-weight:600;color:var(--ink)}

/* header */
.site-header{left:0;top:0;width:1200px;height:100px;background:var(--white);box-shadow:0 2px 6px rgba(0,0,0,.08);z-index:2}
.header-brand{left:112px;top:24px;width:120px;font-size:17px}
.main-nav a{position:absolute;top:40px;font-size:16px;color:var(--ink);text-decoration:none}
.main-nav .active{font-weight:700}
.main-nav .active::after{content:"";position:absolute;left:0;right:0;top:28px;height:2px;background:var(--ink)}

/* hero */
.hero{left:0;top:100px;width:1200px;height:434px;background:var(--hero-bg)}
.hero-photo{left:620px;top:100px;width:580px;height:434px;background:linear-gradient(90deg,var(--hero-bg),var(--photo-warm) 45%,#cbb8a5)}
.hero-title{left:112px;top:182px;width:640px;font-size:37px;line-height:49px;white-space:nowrap}
.hero-copy{left:112px;top:309px;width:445px;font-size:15.5px;line-height:23.5px}
.rating-badge{left:885px;top:473px;width:207px;height:77px;background:var(--white);box-shadow:0 2px 10px rgba(0,0,0,.15);border-radius:3px}
.rating-badge .mark{position:absolute;left:14px;top:15px;width:48px;height:48px;border-radius:50%;background:var(--ink)}
.rating-badge .name{position:absolute;left:82px;top:13px;font-size:17px;font-weight:700;color:var(--ink)}
.rating-badge .score{position:absolute;left:82px;top:42px;font-size:15px;font-weight:700;color:var(--ink)}
.rating-badge .stars{position:absolute;left:112px;top:41px;font-size:14px;color:var(--star);letter-spacing:3px}

/* services */
.service-icon{width:90px;height:90px;border-radius:50%;background:var(--ink);top:622px;display:flex;align-items:center;justify-content:center}
.service-label{top:636px;font-size:19px;line-height:27px;font-weight:600;color:var(--ink)}
.divider{top:626px;width:2px;height:80px;background:var(--ink)}

/* about */
.section-title{font-size:38px}
.body-copy{font-size:15.5px;line-height:23.3px}
.about-visual{left:124px;top:1174px;width:917px;height:349px;background:linear-gradient(90deg,#c7d3da,var(--photo-cool) 40%,#dfe8ee)}
.about-frame{left:193px;top:1303px;width:884px;height:253px;border:1.5px solid var(--ink)}
.deco-circle{left:960px;top:1117px;width:140px;height:140px;border-radius:50%;background:#c9cccd}
.deco-dots{left:58px;top:1462px;width:104px;height:105px;background:#d5d7d8}
.visual-brand{left:640px;top:1340px;width:300px;font-size:40px;color:#6e7a80}
.visual-brand small{display:block;font-size:26px}

/* join */
.join{left:0;top:1643px;width:1200px;height:467px;background:linear-gradient(90deg,#d6d7d9,var(--panel) 30%,#eceded 70%,#dcdddf)}
.join-title{left:0;top:1715px;width:1200px;text-align:center;font-size:38px}
.join-copy{left:165px;top:1806px;width:870px;text-align:center;font-size:15.5px;line-height:23.3px}

/* team */
.team-photo{top:2435px;width:298px;height:303px;background:var(--photo-grey)}
.team-figure{top:2380px;width:200px;height:358px;border-radius:90px 90px 0 0;background:linear-gradient(180deg,#b9b2aa,#f3f3f3 45%)}
.team-name{top:2760px;font-size:19px;font-weight:600;color:var(--ink)}
.team-role{top:2793px;font-size:14px;color:var(--muted)}

/* footer */
.site-footer{left:0;top:2893px;width:1200px;height:277px;background:var(--ink)}
.footer-brand{left:500px;top:2955px;width:200px;font-size:30px;color:var(--white)}
.footer-brand small{display:block;font-size:17px}
.footer-nav a{position:absolute;top:3068px;font-size:19px;color:var(--white);text-decoration:none}
.footer-rule{left:0;top:3122px;width:1200px;height:1px;background:#51606a}
.copyright{left:0;top:3132px;width:1200px;text-align:center;font-size:14px;color:var(--white)}
</style>
</head>
<body>

<header class="abs site-header">
  <div class="abs brand-name header-brand">BRAMBLEFORD<br><span style="font-size:12px">DENTAL PRACTICE</span></div>
  <nav class="main-nav">
    <a class="active" href="#" style="left:429px">Home</a>
    <a href="#" style="left:520px">About</a>
    <a href="#" style="left:608px">New Patients</a>
    <a href="#" style="left:750px">Treatments</a>
    <a href="#" style="left:880px">Fees</a>
  </nav>
  <a class="btn btn-outline" href="#" style="left:962px;top:33px;width:126px;text-decoration:none">Contact Us</a>
</header>

<section>
  <div class="abs hero"></div>
  <div class="abs hero-photo" role="img" aria-label="Smiling woman in a knitted jumper in front of a line sketch of the practice building"></div>
  <h1 class="abs hero-title">Smile with Confidence at<br>Brambleford Dental Practice</h1>
  <p class="abs hero-copy">At our practice, we believe that a visit to the dentist should be a comfortable and positive experience. We strive to create a warm and welcoming atmosphere where our patients can feel at ease and confident in the care they receive.</p>
  <a class="btn btn-dark" href="#" style="left:112px;top:414px;width:126px;text-decoration:none">Book Now</a>
  <div class="abs rating-badge">
    <span class="mark"></span>
    <span class="name">Ravelle</span>
    <span class="score">5.0</span>
    <span class="stars">★★★★★</span>
  </div>
</section>

<section>
  <div class="abs service-icon" style="left:112px">
    <svg width="46" height="46" viewBox="0 0 46 46" fill="none" stroke="#fff" stroke-width="2"><path d="M8 30h22l6-10M14 30l-4-14h10M20 38v-8M12 40h18M30 8v10h6"/></svg>
  </div>
  <div class="abs service-label" style="left:225px">General &amp;<br>Cosmetic Dentistry</div>
  <div class="abs divider" style="left:439px"></div>
  <div class="abs service-icon" style="left:482px">
    <svg width="48" height="40" viewBox="0 0 48 40" fill="none" stroke="#fff" stroke-width="2"><rect x="4" y="6" width="40" height="12" rx="5"/><rect x="4" y="22" width="40" height="12" rx="5"/><path d="M4 12h40M4 28h40"/></svg>
  </div>
  <div class="abs service-label" style="left:596px;top:650px">Orthodontics</div>
  <div class="abs divider" style="left:783px"></div>
  <div class="abs service-icon" style="left:826px">
    <svg width="48" height="48" viewBox="0 0 48 48" fill="none" stroke="#fff" stroke-width="2"><path d="M14 36V24a10 10 0 0 1 20 0v12M10 36h28v4H10zM24 6v5M10 12l3 3M38 12l-3 3"/></svg>
  </div>
  <div class="abs service-label" style="left:940px;top:650px">Emergency Care</div>
</section>

<section>
  <h2 class="abs section-title" style="left:112px;top:788px">About Us</h2>
  <p class="abs body-copy" style="left:112px;top:860px;width:460px">Welcome to our friendly dental practice nestled in the heart of beautiful Harrowmere, UK. Our team of dedicated dentists, hygienists and support staff are here to provide you with exceptional dental care. With a wide array of services, including general and cosmetic dentistry, orthodontics and emergency care, we’re confident that we can deliver the highest quality treatment to you and your loved ones.</p>
  <p class="abs body-copy" style="left:112px;top:1037px;width:460px">At our practice, we believe that a visit to the dentist should be a comfortable and positive experience. We strive to create a warm and welcoming atmosphere where our patients can feel at ease and confident in the care they receive.</p>
  <p class="abs body-copy" style="left:634px;top:860px;width:460px">Our state-of-the-art facilities and equipment mean that you can trust us to deliver the latest techniques and treatments to ensure your oral health is at its best. We are passionate about improving dental health and &nbsp;helping you achieve your brightest smile and are honoured that you’re considering us for your dental needs.</p>
  <a class="btn btn-outline" href="#" style="left:634px;top:1021px;width:126px;text-decoration:none">Read More</a>

  <div class="abs deco-circle" role="img" aria-label="Hatched decorative circle"></div>
  <div class="abs about-frame"></div>
  <div class="abs deco-dots" role="img" aria-label="Decorative dot grid"></div>
  <div class="abs about-visual" role="img" aria-label="Smiling man in a denim jacket beside a pale wall"></div>
  <div class="abs brand-name visual-brand">BRAMBLEFORD<small>DENTAL PRACTICE</small></div>
</section>

<section>
  <div class="abs join" role="img" aria-label="Soft blurred grey interior backdrop"></div>
  <h2 class="abs join-title">Join Our Practice</h2>
  <p class="abs join-copy">If you’re looking for an exceptional dental practice, we’re here to help! Our team is made up of highly skilled professionals who are dedicated to ensuring that all our patients receive top-notch care in a welcoming and comfortable environment. Whether you need a routine examination or a more specialised treatment, we have all the resources to provide you with the best dental care possible. Our practice is always up-to-date with the latest techniques and technologies to make sure that our patients receive the best possible results.<br>We understand that dental care can be expensive which is why we offer affordable prices to ensure that everyone has access to quality care. If you’d like to learn more about our practice, please don’t hesitate to contact us.</p>
  <a class="btn btn-dark" href="#" style="left:537px;top:1991px;width:126px;text-decoration:none">Book Now</a>
</section>

<section>
  <h2 class="abs section-title" style="left:112px;top:2184px">Our Team</h2>
  <p class="abs body-copy" style="left:112px;top:2252px;width:760px">We are delighted to introduce you to our experienced and compassionate dental team. Our team comprises highly skilled dental professionals who are dedicated to providing you with high-quality dental care services. Led by our experienced dentist, each member of our team brings their own unique set of skills and expertise.</p>
  <a class="btn btn-outline" href="#" style="left:958px;top:2259px;width:126px;text-decoration:none">View More</a>

  <div class="abs team-photo" style="left:113px"></div>
  <div class="abs team-figure" style="left:162px" role="img" aria-label="Dentist in a white coat with stethoscope, arms crossed"></div>
  <div class="abs team-name" style="left:113px">Marcus Hale</div>
  <div class="abs team-role" style="left:113px">Co-Founder</div>

  <div class="abs team-photo" style="left:452px"></div>
  <div class="abs team-figure" style="left:501px" role="img" aria-label="Dentist in a white coat and blue tie, arms crossed"></div>
  <div class="abs team-name" style="left:452px">Daniel Ashby</div>
  <div class="abs team-role" style="left:452px">Co-Founder</div>

  <div class="abs team-photo" style="left:790px"></div>
  <div class="abs team-figure" style="left:839px" role="img" aria-label="Dentist in a white coat with stethoscope, arms crossed"></div>
  <div class="abs team-name" style="left:790px">Clara Wynne</div>
  <div class="abs team-role" style="left:790px">Co-Founder</div>
</section>

<footer>
  <div class="abs site-footer"></div>
  <div class="abs brand-name footer-brand">BRAMBLEFORD<small>DENTAL PRACTICE</small></div>
  <nav class="footer-nav">
    <a href="#" style="left:248px">Home</a>
    <a href="#" style="left:350px">About</a>
    <a href="#" style="left:453px">New Patients</a>
    <a href="#" style="left:617px">Treatments</a>
    <a href="#" style="left:767px">Fees</a>
    <a href="#" style="left:856px">Contact Us</a>
  </nav>
  <div class="abs footer-rule"></div>
  <p class="abs copyright">© 2025 Brambleford Dental Practice. All rights reserved.</p>
</footer>

</body>
</html>
```